Flyer for spiritual retreat (yoga, meditation, reiki, raw food)

I would like a flyer to promote my upcoming retreat and a matching Facebook banner.

The name of the retreat is "OutBloom the Spirit" and the tagline is "retreat into you"

The activities in the retreat include daily meditation, ecstatic dance, spiritual development workshops on intuition, energy healing etc and a reiki session is included.

I would like a flyer designed to promote this, something that is editable as I will be running this multiple times and will need to adjust the flyer to add the dates etc each time.

edit: add that here will be fully catered raw food and juices, and that the retreat price includes all accomodation, meals and workshops.

Please contact me if you need further info. Please also visit my website www.marlavosk.com and www.pagenest.com/koruhaven to see my current events and promotions.

Thank you,

Marla

Reason: Hi all, thank you all for your submissions. Apologies as I am traveling and do not have much access to internet and will review your submissions and provide feedback as soon as possible. Kind regards, Marla.

Target Market(s)

People who like meditation, yoga, fans of tomas brenner and wendell marsh, those interested in personal and spiritual development.

Industry/Entity Type

Health And Wellness

Requirements
Must have
• Please put the included reiki session as as added bonus. Something like "BONUS 30 minute reiki healing session" in a little star/banner/something that stands out.
• Please emphasise the "light" part of OutBloom as I am going for a play on words between in the light and enlightenment.
• Please include placeholder text for place, location, time
• Placeholder for price
• My name (see attached file - can change colour to suit) and website (www.marlavosk.com)
Nice to have
• I prefer rounded designs, curves rather than block designs.
Should not have
• Koru Haven logo

```html
<!DOCTYPE html>
<html lang="en">
<head>
<meta charset="utf-8">
<title>OutBloom the Spirit – Retreat Flyer</title>
<link rel="stylesheet" href="https://fonts.googleapis.com/css2?family=Raleway:wght@400;500&family=Nunito:wght@400;600&family=Great+Vibes&display=swap">
<style>
  :root{
    --violet-top:#c68bbd;
    --violet-bottom:#8a7fc0;
    --pink-stripe:#e8a6cb;
    --mist:#eef3e6;
    --mist-edge:#dfe9d4;
    --ink:#7b4d9d;
    --glow:#f2e428;
    --white:#ffffff;
    --date-a:#8b6cc0;
    --date-b:#b879b8;
    --price-disc:#c68bbd;
  }
  *{margin:0;padding:0;box-sizing:border-box}
  html,body{width:912px;height:1200px;overflow:hidden;background:#e4e4e4}
  .flyer{position:relative;width:912px;height:1200px;overflow:hidden;
    background:linear-gradient(180deg,var(--violet-top) 0%,#b48bc2 40%,var(--violet-bottom) 100%);
    font-family:"Nunito",sans-serif;color:var(--ink)}
  .backdrop{position:absolute;inset:0}
  .title{position:absolute;top:52px;left:0;width:912px;text-align:center;
    font-family:"Raleway",sans-serif;font-weight:400;font-size:55px;letter-spacing:3px;color:var(--white)}
  .title .glow{color:var(--glow)}
  .tagline{position:absolute;top:212px;left:470px;font-family:"Great Vibes",cursive;font-size:62px;color:var(--ink)}
  .features{position:absolute;top:328px;left:513px;list-style:none}
  .features li{display:flex;align-items:center;height:50px;font-weight:600;font-size:19px;letter-spacing:.5px;text-transform:uppercase}
  .features svg{width:24px;height:24px;margin-right:14px}
  .dates{position:absolute;top:722px;left:72px;font-family:"Raleway",sans-serif;font-weight:400;font-size:80px;line-height:78px;
    background:linear-gradient(90deg,var(--date-b),var(--date-a) 60%,#7a84c8);-webkit-background-clip:text;background-clip:text;color:transparent}
  .divider{position:absolute;left:538px;top:736px;width:2px;height:106px;background:var(--ink)}
  .location{position:absolute;top:737px;left:576px;font-size:19px;line-height:34px;letter-spacing:.5px}
  .price-block{position:absolute;top:982px;left:75px;color:var(--white)}
  .price{font-family:"Raleway",sans-serif;font-size:48px;line-height:48px;display:flex;align-items:flex-start}
  .price small{font-family:"Nunito",sans-serif;font-size:17px;line-height:15px;margin:6px 0 0 8px}
  .includes{margin-top:14px;font-size:17px;line-height:22px;letter-spacing:.3px;width:290px}
  .bonus{margin-top:16px;font-size:17px;line-height:22px;letter-spacing:.3px;width:290px}
  .host{position:absolute;right:48px;top:920px;text-align:right;color:var(--white)}
  .host-label{font-size:18px;letter-spacing:.5px}
  .host-name{font-family:"Great Vibes",cursive;font-size:80px;line-height:90px;margin-right:30px}
  .web{font-family:"Raleway",sans-serif;font-size:23px;letter-spacing:1px;margin-top:0}
  .mail{font-family:"Raleway",sans-serif;font-size:23px;letter-spacing:1px;margin-top:14px;display:flex;align-items:center;justify-content:flex-end}
  .mail svg{width:26px;height:18px;margin-right:20px}
</style>
</head>
<body>
<main class="flyer">
  <svg class="backdrop" width="912" height="1200" viewBox="0 0 912 1200">
    <defs>
      <radialGradient id="mistFill" cx="0.6" cy="0.55" r="0.7">
        <stop offset="0" stop-color="#fbfbf6"/>
        <stop offset="0.6" stop-color="var(--mist)"/>
        <stop offset="1" stop-color="var(--mist-edge)"/>
      </radialGradient>
      <linearGradient id="portraitFill" x1="0" y1="0" x2="1" y2="1">
        <stop offset="0" stop-color="#9fbf86"/>
        <stop offset="0.5" stop-color="#5b4a55"/>
        <stop offset="1" stop-color="#b3a6c9"/>
      </linearGradient>
    </defs>
    <path class="stripe-top" d="M300,200 Q600,140 912,150 L912,176 Q600,160 300,214 Z" fill="var(--pink-stripe)"/>
    <path class="mist-panel" role="img" aria-label="Soft misty garden backdrop with a white water lily on still water"
      d="M0,236 Q450,150 912,171 L912,736 C720,880 520,950 376,973 L0,973 Z" fill="url(#mistFill)"/>
    <path class="stripe-bottom" d="M912,716 C720,870 520,945 376,973 L390,980 C540,955 730,890 912,750 Z" fill="var(--pink-stripe)"/>
    <circle class="portrait" role="img" aria-label="Portrait of the host in a garden, hands pressed together in prayer" cx="232" cy="425" r="222" fill="url(#portraitFill)"/>
    <circle class="price-disc" cx="110" cy="1240" r="320" fill="var(--price-disc)" stroke="var(--white)" stroke-width="5"/>
  </svg>

  <h1 class="title">OUT<span class="glow">BLOOM</span> THE SPIRIT</h1>
  <p class="tagline">Retreat into You</p>

  <ul class="features">
    <li><svg viewBox="0 0 24 24"><path d="M3 13 L9 20 L22 4" fill="none" stroke="var(--pink-stripe)" stroke-width="3" stroke-linecap="round"/></svg>Daily Meditation</li>
    <li><svg viewBox="0 0 24 24"><path d="M3 13 L9 20 L22 4" fill="none" stroke="var(--pink-stripe)" stroke-width="3" stroke-linecap="round"/></svg>Ecstatic Dance</li>
    <li><svg viewBox="0 0 24 24"><path d="M3 13 L9 20 L22 4" fill="none" stroke="var(--pink-stripe)" stroke-width="3" stroke-linecap="round"/></svg>Intuition Workshops</li>
    <li><svg viewBox="0 0 24 24"><path d="M3 13 L9 20 L22 4" fill="none" stroke="var(--pink-stripe)" stroke-width="3" stroke-linecap="round"/></svg>Energy Healing</li>
    <li><svg viewBox="0 0 24 24"><path d="M3 13 L9 20 L22 4" fill="none" stroke="var(--pink-stripe)" stroke-width="3" stroke-linecap="round"/></svg>Spiritual Development</li>
    <li><svg viewBox="0 0 24 24"><path d="M3 13 L9 20 L22 4" fill="none" stroke="var(--pink-stripe)" stroke-width="3" stroke-linecap="round"/></svg>Raw Food &amp; Juices</li>
    <li><svg viewBox="0 0 24 24"><path d="M3 13 L9 20 L22 4" fill="none" stroke="var(--pink-stripe)" stroke-width="3" stroke-linecap="round"/></svg>Accomodation Included</li>
  </ul>

  <div class="dates">NOV 24-28<br>2016</div>
  <div class="divider"></div>
  <address class="location" style="font-style:normal">Location: 14/32<br>Wattle Bend,<br>Ashdale Perth</address>

  <section class="price-block">
    <div class="price">$500<small>per<br>person</small></div>
    <p class="includes">INCLUDES: all accomodation, meals &amp; workshops</p>
    <p class="bonus">BONUS: 30 min Reiki Healing Session</p>
  </section>

  <section class="host">
    <div class="host-label">Hosted By:</div>
    <div class="host-name">Marla Vosk</div>
    <div class="web">www.marlavosk.com</div>
    <div class="mail"><svg viewBox="0 0 26 18"><rect x="0" y="0" width="26" height="18" rx="1" fill="var(--white)"/><path d="M1 1 L13 10 L25 1" fill="none" stroke="#9a82c0" stroke-width="2"/></svg>marlavosk33@mailbox.com</div>
  </section>
</main>
</body>
</html>
```